Business Folder

I need a fresh, modern design for a business folder. I have our company's colors, logo, and a separate file for just the graphic part of our logo as a design element. No photo, just colors, gradients, and shadows to create depth. I like the idea of a rich grey as the background, however, I realize we'd have to lighten to 'Tax Advisory Services' part of our logo.

The design would just be the 'front' or outside of the folder from PressVale. Design file attached. You can find that here under 9 x 12 standard folder, Left and Right Pockets With Slit Both Sides:

https://www.pressvale-example.com/content.html?id=folderDownloadTemplates&rightMenuId=rightMenu&footerId=bodyFooterStyle6

```html
<!DOCTYPE html>
<html lang="en">
<head>
<meta charset="utf-8">
<title>Lumera Business Folder – Outside Spread</title>
<link rel="stylesheet" href="https://fonts.googleapis.com/css2?family=Lato:wght@400;700;900&display=swap">
<style>
  :root {
    --stage: #d9dadc;
    --grey-rich: #4a4f56;
    --grey-deep: #363a40;
    --grey-soft: #5d636b;
    --navy-deep: #083d69;
    --navy: #0b4c80;
    --blue-mid: #1c87c2;
    --blue-bright: #2fa2db;
    --cyan: #5cc6e6;
    --brand-light: #ffffff;
    --tagline-light: #d3dae3;
    --ink-light: #ffffff;
  }
  * { margin: 0; padding: 0; box-sizing: border-box; }
  html, body { width: 1200px; height: 847px; overflow: hidden; }
  body {
    background: var(--stage);
    font-family: "Lato", Arial, sans-serif;
    position: relative;
  }
  .folder-spread {
    position: absolute;
    left: 30px;
    top: 43px;
    width: 1140px;
    height: 760px;
    display: flex;
    box-shadow: 0 10px 30px rgba(0,0,0,0.25);
    overflow: hidden;
  }
  .panel {
    position: relative;
    width: 570px;
    height: 760px;
    background: linear-gradient(160deg, var(--grey-soft) 0%, var(--grey-rich) 45%, var(--grey-deep) 100%);
  }
  .panel--back { border-right: 1px solid rgba(0,0,0,0.25); }
  .band-top {
    position: absolute;
    left: 0; top: 0;
    width: 100%; height: 190px;
    background: linear-gradient(180deg, var(--navy) 0%, var(--blue-mid) 70%, var(--blue-bright) 100%);
  }
  .band-top-accent {
    position: absolute;
    left: 0; top: 190px;
    width: 100%; height: 14px;
    background: linear-gradient(90deg, var(--cyan), var(--blue-bright));
  }
  .band-bottom {
    position: absolute;
    left: 0; bottom: 0;
    width: 100%; height: 230px;
    background: linear-gradient(180deg, var(--blue-mid) 0%, var(--navy) 40%, var(--navy-deep) 100%);
  }
  .band-bottom-accent {
    position: absolute;
    left: 0; bottom: 230px;
    width: 100%; height: 14px;
    background: linear-gradient(90deg, var(--blue-bright), var(--cyan));
  }
  .brand-lockup {
    position: absolute;
    left: 80px;
    top: 318px;
  }
  .brand-row { display: flex; align-items: center; gap: 16px; }
  .brand-mark {
    width: 44px; height: 44px;
    background: var(--blue-bright);
  }
  .brand-name {
    font-weight: 900;
    font-size: 64px;
    line-height: 1;
    letter-spacing: 4px;
    color: var(--brand-light);
  }
  .brand-tagline {
    margin: 12px 0 0 60px;
    font-weight: 400;
    font-size: 16px;
    letter-spacing: 4px;
    color: var(--tagline-light);
  }
  .contact-block {
    position: absolute;
    right: 26px;
    bottom: 96px;
    text-align: right;
    color: var(--ink-light);
  }
  .contact-heading { font-weight: 700; font-size: 17px; margin-bottom: 6px; }
  .contact-line { font-weight: 400; font-size: 13px; line-height: 20px; }
  .contact-phone { margin-top: 6px; }
</style>
</head>
<body>
  <main class="folder-spread" aria-label="Folder outside spread: back cover left, front cover right">
    <section class="panel panel--back">
      <div class="band-top" role="img" aria-label="Blue brand band with layered geometric facets"></div>
      <div class="band-top-accent"></div>
      <div class="band-bottom-accent"></div>
      <div class="band-bottom" role="img" aria-label="Blue brand band with layered geometric facets"></div>
      <address class="contact-block" style="font-style: normal;">
        <p class="contact-heading">Address:</p>
        <p class="contact-line">Lorem ipsum dolor sit amet,</p>
        <p class="contact-line">consectetuer adipiscing elit, sed diam</p>
        <p class="contact-line">nonummy nibh</p>
        <p class="contact-line contact-phone">Ph: 0000 000 000, Fax: 0000 000 000</p>
      </address>
    </section>
    <section class="panel panel--front">
      <div class="band-top" role="img" aria-label="Blue brand band with layered geometric facets"></div>
      <div class="band-top-accent"></div>
      <div class="brand-lockup">
        <div class="brand-row">
          <span class="brand-mark"></span>
          <span class="brand-name">LUMERA</span>
        </div>
        <p class="brand-tagline">TAX ADVISORY SERVICES</p>
      </div>
      <div class="band-bottom-accent"></div>
      <div class="band-bottom" role="img" aria-label="Blue brand band with layered geometric facets"></div>
    </section>
  </main>
</body>
</html>
```